Website Design Request - Management Consulting Firm

We need a Website designed for an IT Management Staffing and Recruiting firm called TRAVENOK based in San Francisco.

The firm is an high-end technology staffing agency. Our focus is on quality and high-caliber candidates rather than quantity.

The website will have two main home pages. One for the recruiter and another on for the candidates.

The website needs to optimize for mobile devices as well.

I have attached few mock-ups that I have done just to show what I am thinking. The UI needs to be very clean, fluid, and it needs to have a modern, rustic, professional feel to it.

Target Market(s)

Technology Manager, Director, VP, CIO of Companies that have $4b-10b dollar revenue. Such as larkspurdwellings.example , https://www.velmorian.example/, quillnet.example, zib.example

Industry/Entity Type

Management Consulting

Number of Pages Required

5+ page

Font styles to use
Sans Serif

Colors
f37122
ffffff

Requirements
Must have
• Please review mock-ups for suggestions
Nice to have
Should not have

```html
<!DOCTYPE html>
<html lang="en">
<head>
<meta charset="utf-8">
<title>TRAVENOK — IT Project Management Jobs</title>
<link rel="stylesheet" href="https://fonts.googleapis.com/css2?family=Open+Sans:wght@300;400;600;700&display=swap">
<style>
:root{
  --orange:#f37122;
  --orange-dark:#d95c12;
  --white:#ffffff;
  --ink:#444444;
  --muted:#8a8a8a;
  --light:#bdbdbd;
  --tab-grey:#c9c9c9;
  --footer:#e9e9e9;
  --footer-text:#6f6f6f;
}
*{box-sizing:border-box;margin:0;padding:0}
html,body{width:841px;height:1200px;overflow:hidden;background:var(--white)}
body{font-family:"Open Sans",Arial,sans-serif;color:var(--ink);position:relative}

.site-header{height:62px;display:flex;align-items:center;justify-content:space-between;padding:0 58px 0 108px}
.brand{display:flex;align-items:center;gap:8px;font-weight:700;font-size:26px;letter-spacing:1px;color:var(--orange)}
.brand-dot{width:12px;height:12px;border-radius:50%;background:var(--orange)}
.main-nav{display:flex;gap:34px;font-size:13px;color:var(--ink)}

.hero{position:relative;height:343px;text-align:center;color:var(--white);overflow:hidden}
.hero-photo{position:absolute;inset:0;background:linear-gradient(180deg,#f58a45 0%,#f37122 55%,#e8661b 100%)}
.hero-content{position:relative;padding-top:88px}
.hero-title{font-size:30px;font-weight:400;letter-spacing:.2px}
.hero-sub{font-size:17px;font-weight:300;margin-top:6px;opacity:.95}
.signup{display:flex;flex-direction:column;align-items:center;margin-top:24px;gap:12px}
.email-field{width:316px;height:30px;background:var(--white);border-radius:2px;text-align:left;padding:7px 12px;font-size:11px;color:var(--light)}
.cta-dark{width:202px;height:30px;background:#2f2f2f;color:var(--white);font-size:13px;display:flex;align-items:center;justify-content:center;border-radius:2px}
.employer-note{font-size:9px;opacity:.9}
.employer-note u{text-decoration:underline}
.carousel-dots{display:flex;justify-content:center;gap:7px;margin-top:30px}
.carousel-dots span{width:9px;height:9px;border-radius:50%;border:1.5px solid var(--white)}
.carousel-dots span.active{background:var(--white)}

.tabs{height:37px;background:var(--tab-grey);display:flex;justify-content:center}
.tab{width:144px;display:flex;align-items:center;justify-content:center;font-size:14px;color:var(--white)}
.tab.active{background:var(--orange);position:relative}
.tab.active::after{content:"";position:absolute;bottom:-8px;left:50%;margin-left:-8px;border:8px solid transparent;border-bottom:0;border-top-color:var(--orange)}

.steps-intro{text-align:center;padding-top:42px}
.steps-intro h2{font-size:15px;font-weight:400;color:var(--ink)}
.steps-intro p{font-size:13px;font-weight:300;color:var(--muted);margin-top:8px}

.step-list{list-style:none;margin-top:44px;padding-left:192px}
.step{display:flex;align-items:center;height:108px}
.step-icon{width:70px;height:70px;display:flex;align-items:center;justify-content:center}
.step-number{width:58px;font-size:54px;font-weight:300;color:#d5d5d5;text-align:center;margin-left:22px}
.step-text h3{font-size:18px;font-weight:400;color:var(--ink)}
.step-text p{font-size:10px;color:var(--muted);margin-top:5px;max-width:230px;line-height:1.45}

.upload-cta{display:flex;justify-content:center;margin-top:36px}
.btn-outline{height:38px;padding:0 22px;border:1.5px solid var(--orange);border-radius:20px;display:flex;align-items:center;gap:8px;font-size:13px;color:var(--orange)}

.site-footer{position:absolute;left:0;right:0;top:995px;bottom:0;background:var(--footer);padding:30px 0 0 120px}
.footer-cols{display:flex;gap:0}
.footer-col{width:130px}
.footer-col h4{font-size:14px;font-weight:400;color:var(--ink);margin-bottom:8px}
.footer-col li{list-style:none;font-size:9px;color:var(--footer-text);line-height:1.9}
.social-row{display:flex;gap:6px;margin-bottom:16px}
.social-row span{width:20px;height:20px;border-radius:50%;background:var(--orange)}
.footer-brand{font-size:28px;font-weight:700;letter-spacing:1px;color:#9b9b9b}
.copyright{font-size:9px;color:var(--footer-text);margin-top:18px}
</style>
</head>
<body>

<header class="site-header">
  <div class="brand"><span class="brand-dot"></span>TRAVENOK</div>
  <nav class="main-nav">
    <span>Professionals</span><span>Employers</span><span>Sign In</span><span>Sign Up</span>
  </nav>
</header>

<section class="hero">
  <div class="hero-photo" role="img" aria-label="Photo of professionals working together at a laptop, tinted orange"></div>
  <div class="hero-content">
    <h1 class="hero-title">Looking for IT Project Management Jobs?</h1>
    <p class="hero-sub">Upload your resume, accept interview requests, get offer</p>
    <div class="signup">
      <div class="email-field">Your Email address</div>
      <div class="cta-dark">Get Offers Now</div>
      <p class="employer-note">Looking for talent? <u>See how it works for Employers</u></p>
    </div>
    <div class="carousel-dots"><span class="active"></span><span></span><span></span><span></span></div>
  </div>
</section>

<nav class="tabs">
  <div class="tab active">How it Works</div>
  <div class="tab">Why Us?</div>
</nav>

<section class="steps">
  <div class="steps-intro">
    <h2>3 Simple Steps</h2>
    <p>Employers pay 25% more for a better IT Project Manager</p>
  </div>

  <ol class="step-list">
    <li class="step">
      <div class="step-icon">
        <svg width="62" height="50" viewBox="0 0 62 50" fill="none" stroke="#f37122" stroke-width="2.5" stroke-linecap="round" stroke-linejoin="round">
          <path d="M17 38H13a10 10 0 0 1-1-20 15 15 0 0 1 29-4 11 11 0 0 1 9 24h-5"/>
          <path d="M31 48V24M23 32l8-8 8 8"/>
        </svg>
      </div>
      <div class="step-number">1</div>
      <div class="step-text">
        <h3>Upload your Resume</h3>
        <p>Answer few questions and upload your resume</p>
      </div>
    </li>
    <li class="step">
      <div class="step-icon">
        <svg width="56" height="40" viewBox="0 0 56 40" fill="none" stroke="#f37122" stroke-width="2.5" stroke-linejoin="round">
          <rect x="2" y="2" width="52" height="36" rx="2"/>
          <path d="M2 3l26 20L54 3M2 37l19-18M54 37L35 19"/>
        </svg>
      </div>
      <div class="step-number">2</div>
      <div class="step-text">
        <h3>We Send You Interview Requests</h3>
        <p>Interested in someone? With a single click, send interview request and let us handle the rest</p>
      </div>
    </li>
    <li class="step">
      <div class="step-icon">
        <svg width="56" height="56" viewBox="0 0 56 56" fill="none" stroke="#f37122" stroke-width="2.5" stroke-linecap="round" stroke-linejoin="round">
          <circle cx="30" cy="18" r="13"/>
          <path d="M34 12h-6a3 3 0 0 0 0 6h4a3 3 0 0 1 0 6h-6M30 9v3M30 24v3"/>
          <path d="M4 42h8l10 6h16l12-9-3-3-11 5H26"/>
        </svg>
      </div>
      <div class="step-number">3</div>
      <div class="step-text">
        <h3>Get $1000 Bonus</h3>
        <p>Find a Job and get $1000 bonus TRAVENOK</p>
      </div>
    </li>
  </ol>

  <div class="upload-cta">
    <div class="btn-outline">
      <svg width="16" height="14" viewBox="0 0 16 14" fill="none" stroke="#f37122" stroke-width="1.6" stroke-linecap="round" stroke-linejoin="round"><path d="M5 11H4a3 3 0 0 1 0-6 4.5 4.5 0 0 1 8.6-1A3 3 0 0 1 12 11h-1M8 13V6M5.5 8.5L8 6l2.5 2.5"/></svg>
      Upload Your Resume
    </div>
  </div>
</section>

<footer class="site-footer">
  <div class="footer-cols">
    <div class="footer-col">
      <h4>Company</h4>
      <ul><li>About</li><li>Who We Are</li><li>Media Kit</li><li>Our Team</li></ul>
    </div>
    <div class="footer-col">
      <h4>SubHubs</h4>
      <ul><li>Recruiting</li><li>Employers</li><li>Professionals</li><li>Job Kit</li></ul>
    </div>
    <div class="footer-col">
      <h4>Resources</h4>
      <ul><li>Terms of Use</li><li>Support</li><li>Privacy Policy</li><li>Contact Us</li></ul>
    </div>
    <div class="footer-col follow">
      <h4>Follow Us</h4>
      <div class="social-row"><span></span><span></span><span></span><span></span><span></span></div>
      <div class="footer-brand">TRAVENOK</div>
    </div>
  </div>
  <p class="copyright">© 2016 Company Name. All rights reserved</p>
</footer>

</body>
</html>
```